Pull Up Banner - Recruitment Company

We would like a design for a pull up banner.

For context: we are a recruitment business. We specialise in helping people in healthcare industry to find jobs in Australia.

I have come up with several ideas and text for the banner. Feel free to use the following as you see appropriate:

- Our logo (see attached)
- 'Healthcare Recruitment Agency'
- Some sort of imagine / cartoon of medical professionals (ie. doctor, nurse, physiotherapist, speech pathologist). A cartoon is more friendly than committing to a photo
- 'Empowering your next career move'
- 'Discover tailored opportunities based on your career preferences'
- Dot points (allied health, nursing, medical imaging)
- Contact info at the bottom including our website (www.quellastaffing.com.au, our Instagram handle @quellastaffing, Mobile: XXXX XXX XXX. The title section for contact information could be 'Get in touch:'

Feel free to submit a couple of designs and we can merge aspects that look good on your designs and find the perfect fit.
Thank you
Updates

Hello,

Thank you for your initial submissions to this project. I appreciate the time you've invested.

After reviewing the first attempt, I'd like to share some feedback and initial observations:

- Professionalism and engagement: Is the overall appearance of the banner professional? It's crucial that we have a high-quality design as this will represent our business.

- Image selection: The image (whether cartoon or real people) appears quite generic. Please consider submitting the banner with a few different photos in the middle for us to choose from. Ensure the image is a good fit and not simply a generic stock photo.

- Contact section: Kindly remove the phone number; we no longer wish to include it on the banner. Instead, please include our website (www.quellastaffing.com.au) and Instagram handle (@quellastaffing).

- Color scheme: White, black, and red/pink are preferred, or alternatively, blue. However, please avoid incorporating too many different colors as it may detract from the professional appearance.

We will be printing the design on a banner and require it to look professional and engaging.

Thank you once again for your submissions. I hope the feedback provided above is helpful.

Warm regards,

Target Market(s)

Allied Health Australia

Font styles to use
Serif

Colors
0054AA
0677BA
7BADD7
CADEEF
E8F1F8
0094D4
00A9DD
6FCCEA
C7EBF8
E9F6FB
EB3D1F
EC4F4E
F09395
F8D3D4
FCEDEE

```html
<!DOCTYPE html>
<html lang="en">
<head>
<meta charset="utf-8">
<title>Quella Staffing – Healthcare Recruitment Pull Up Banner</title>
<link rel="stylesheet" href="https://fonts.googleapis.com/css2?family=Poppins:wght@400;500;600;700;800&display=swap">
<style>
  :root {
    --stage: #d9d9dc;
    --paper: #ffffff;
    --royal: #2a32c4;
    --ink: #0f1a2b;
    --blush: #f8c9cc;
    --blush-soft: #fce3e4;
    --charcoal: #2d2b2c;
    --rule: #c9c9cf;
    --grey-text: #2a2a2a;
  }
  * { margin: 0; padding: 0; box-sizing: border-box; }
  html, body {
    width: 1200px; height: 2400px; overflow: hidden;
    background: var(--stage);
    font-family: "Poppins", sans-serif;
  }
  .banner {
    position: absolute; left: 83px; top: 0;
    width: 1034px; height: 2400px;
    background: var(--paper);
    overflow: hidden;
  }
  .brand { position: absolute; left: 132px; top: 72px; width: 500px; height: 170px; color: var(--ink); }
  .brand-name {
    position: absolute; left: 0; top: 0;
    font-weight: 800; font-size: 112px; line-height: 1; letter-spacing: 3px;
  }
  .brand-sub {
    position: absolute; left: 282px; top: 132px;
    font-weight: 500; font-size: 26px; letter-spacing: 8px; white-space: nowrap; line-height: 1;
  }
  .headline { position: absolute; left: 0; top: 0; width: 100%; height: 600px; }
  .headline span {
    position: absolute; left: 108px; line-height: 1; white-space: nowrap; font-weight: 800;
  }
  .headline-accent { top: 276px; color: var(--royal); font-size: 124px; }
  .headline-line { color: var(--ink); font-size: 96px; }
  .headline-line.first { top: 397px; }
  .headline-line.second { top: 498px; }
  .artwork {
    position: absolute; left: 40px; top: 605px; width: 954px; height: 733px;
  }
  .tagline-band {
    position: absolute; left: 0; top: 1338px; width: 100%; height: 449px;
    background: var(--royal); color: #fff; text-align: center;
  }
  .tagline-strong {
    position: absolute; top: 51px; width: 100%;
    font-weight: 800; font-size: 88px; line-height: 1;
  }
  .tagline-light {
    position: absolute; top: 140px; width: 100%;
    font-weight: 400; font-size: 90px; line-height: 1;
  }
  .tagline-rule {
    position: absolute; left: 427px; top: 252px; width: 134px; height: 13px;
    background: var(--blush);
  }
  .tagline-copy {
    position: absolute; top: 282px; width: 100%;
    font-weight: 400; font-size: 43px; line-height: 1.2;
  }
  .specialties {
    position: absolute; left: 0; top: 1865px; width: 100%; height: 300px;
  }
  .specialty {
    position: absolute; top: 0; width: 300px; margin-left: -150px; text-align: center;
  }
  .specialty-icon { display: block; margin: 0 auto; }
  .specialty-label {
    margin-top: 40px; font-weight: 500; font-size: 46px; line-height: 1.02;
    color: var(--grey-text);
  }
  .specialty-divider {
    position: absolute; top: 0; width: 3px; height: 260px; background: var(--rule);
  }
  .web-bar {
    position: absolute; left: 102px; top: 2174px; width: 828px; height: 80px;
    background: var(--charcoal); border-radius: 6px;
    color: var(--blush); font-weight: 700; font-size: 50px; line-height: 80px;
    text-align: center; box-shadow: 0 6px 6px rgba(0,0,0,.18);
  }
  .social {
    position: absolute; left: 127px; top: 2264px; height: 56px;
    display: flex; align-items: center; color: var(--ink);
  }
  .social-label { font-weight: 500; font-size: 29px; letter-spacing: 7px; }
  .social-dot {
    width: 38px; height: 38px; border-radius: 50%; background: #e2457a;
    margin: 0 18px 0 24px;
  }
  .social-handle { font-weight: 700; font-size: 44px; }
</style>
</head>
<body>
  <main class="banner">
    <header class="brand">
      <div class="brand-name">QUELLA</div>
      <div class="brand-sub">STAFFING</div>
    </header>

    <h1 class="headline">
      <span class="headline-accent">HEALTHCARE</span>
      <span class="headline-line first">RECRUITMENT</span>
      <span class="headline-line second">AGENCY</span>
    </h1>

    <svg class="artwork" viewBox="0 0 954 733" role="img"
         aria-label="Cartoon illustration of a doctor with a clipboard beside scenes of a speech therapy session, a physiotherapy exercise and a nurse caring for a patient">
      <defs>
        <linearGradient id="artwork-tone" x1="0" y1="0" x2="1" y2="1">
          <stop offset="0" stop-color="#ffffff"/>
          <stop offset="0.55" stop-color="#fce3e4"/>
          <stop offset="1" stop-color="#f8d0d2"/>
        </linearGradient>
      </defs>
      <rect width="954" height="733" fill="url(#artwork-tone)"/>
    </svg>

    <section class="tagline-band">
      <p class="tagline-strong">EMPOWERING YOUR</p>
      <p class="tagline-light">NEXT CAREER MOVE</p>
      <div class="tagline-rule"></div>
      <p class="tagline-copy">Discover tailored opportunities based<br>on your career preferences</p>
    </section>

    <section class="specialties">
      <div class="specialty" style="left:175px">
        <svg class="specialty-icon" width="122" height="122" viewBox="0 0 122 122">
          <circle cx="61" cy="61" r="58" fill="var(--blush-soft)" stroke="var(--royal)" stroke-width="3"/>
          <path d="M61 92 C30 70 24 56 28 45 C33 32 52 30 61 44 C70 30 89 32 94 45 C98 56 92 70 61 92 Z" fill="#111"/>
          <polyline points="32,60 48,60 54,50 61,72 68,54 74,60 90,60" fill="none" stroke="#fff" stroke-width="4" stroke-linejoin="round"/>
        </svg>
        <p class="specialty-label">Allied<br>Health</p>
      </div>
      <div class="specialty-divider" style="left:330px"></div>
      <div class="specialty" style="left:484px">
        <svg class="specialty-icon" width="122" height="122" viewBox="0 0 122 122">
          <circle cx="61" cy="61" r="58" fill="var(--blush-soft)" stroke="var(--royal)" stroke-width="3"/>
          <path d="M38 46 L42 28 L80 28 L84 46 Z" fill="#111"/>
          <rect x="56" y="32" width="10" height="10" fill="#fff"/>
          <path d="M30 96 C32 76 46 68 61 68 C76 68 90 76 92 96 Z" fill="#111"/>
          <rect x="56" y="76" width="10" height="14" fill="#fff"/>
        </svg>
        <p class="specialty-label">Nursing</p>
      </div>
      <div class="specialty-divider" style="left:656px"></div>
      <div class="specialty" style="left:822px">
        <svg class="specialty-icon" width="122" height="122" viewBox="0 0 122 122">
          <circle cx="61" cy="61" r="58" fill="var(--blush-soft)" stroke="var(--royal)" stroke-width="3"/>
          <path d="M61 78 C36 62 32 50 35 42 C39 31 54 30 61 41 C68 30 83 31 87 42 C90 50 86 62 61 78 Z" fill="#111"/>
          <rect x="57" y="42" width="8" height="24" fill="#fff"/>
          <rect x="49" y="50" width="24" height="8" fill="#fff"/>
          <path d="M28 92 L50 84 L78 84 L96 74 L98 82 L80 96 L28 98 Z" fill="#111"/>
        </svg>
        <p class="specialty-label">Medical<br>Imaging</p>
      </div>
    </section>

    <div class="web-bar">www.quellastaffing.com.au</div>

    <footer class="social">
      <span class="social-label">FOLLOW US ON</span>
      <span class="social-dot"></span>
      <span class="social-handle">@quellastaffing</span>
    </footer>
  </main>
</body>
</html>
```